Home Page Enhancement

I am upgrading an existing site and have had a designer help me to create a new look and feel. Whilst I am generally happy with it, I am still not happy with the top half of the page, more specifically the background image on the search box.

I am therefore looking for someone clever and creative to improve on this.

Please see attached files of the new design, plus two examples that could potentially work as improvements.

Target Market(s)

Korean travelers looking to find the best deals and lowest prices on their next hotel stay

Requirements
Must have
• Must emphasise the search box so users are naturally drawn to the search box to initiate a search.
Nice to have
• The background image could potentially emphasize the overall value proposition of the site which is about searching hundreds of travel sites in one search to find you the very best deals.

```html
<!DOCTYPE html>
<html lang="en">
<head>
<meta charset="utf-8">
<title>StayScout – Search Your Best Hotel Now</title>
<link rel="stylesheet" href="https://fonts.googleapis.com/css2?family=Ubuntu:wght@300;400;500;700&family=Open+Sans:wght@400;600;700&display=swap">
<style>
:root{
  --header-blue:#1d5ea9;
  --hero-edge:#17589f;
  --hero-mid:#2a78c1;
  --hero-glow:#5cabe4;
  --heading-blue:#1c5fa6;
  --orange-top:#fdaa3c;
  --orange-dark:#ee7f0c;
  --price-yellow:#ffd400;
  --caption-bg:rgba(20,28,38,.8);
  --gray-band:#e6e6e6;
  --gray-text:#6d6d6d;
  --gray-light:#8a8a8a;
  --gray-icon:#848484;
  --field-border:#c9d6e4;
  --subscribe:#1e8fd6;
  --white:#ffffff;
}
*{box-sizing:border-box;margin:0;padding:0}
html,body{width:719px;height:1200px;overflow:hidden;background:var(--white)}
body{font-family:"Ubuntu",sans-serif;position:relative;color:var(--gray-text)}

.site-header{position:absolute;left:0;top:0;width:719px;height:70px;background:var(--header-blue)}
.brand{position:absolute;left:38px;top:22px;color:var(--white);font:700 25px/1 "Ubuntu",sans-serif;letter-spacing:.4px}
.social{position:absolute;right:38px;top:33px;display:flex;gap:3px}
.social span{width:19px;height:19px;border-radius:50%;background:var(--white);display:block}

.hero{position:absolute;left:0;top:70px;width:719px;height:267px;overflow:hidden;
  background:
    radial-gradient(ellipse 330px 120px at 250px 150px,rgba(120,190,240,.55) 0%,rgba(120,190,240,0) 100%),
    radial-gradient(ellipse at 40% 55%,var(--hero-glow) 0%,var(--hero-mid) 45%,var(--hero-edge) 100%)}
.hero-art{position:absolute;inset:0}
.hero-title{position:absolute;left:38px;top:43px;color:var(--white);font:400 26px/1 "Ubuntu",sans-serif;text-shadow:0 1px 2px rgba(0,40,90,.3)}
.hero-sub{position:absolute;left:38px;top:76px;color:#eaf4fc;font:300 14px/1 "Ubuntu",sans-serif}
.field{position:absolute;background:var(--white);border:1px solid var(--field-border);border-radius:3px;color:#8c8c8c;font:300 10px/1 "Ubuntu",sans-serif;display:flex;align-items:center;padding-left:8px;white-space:nowrap;box-shadow:0 2px 6px rgba(0,40,90,.35)}
.field.select::after{content:"";position:absolute;right:7px;top:50%;margin-top:-2px;border:3.5px solid transparent;border-top:4px solid #8c8c8c;border-bottom:0}
.field.small{font-size:9.5px;padding-left:7px}
.label{position:absolute;color:var(--white);font:400 10px/1 "Ubuntu",sans-serif}
.btn-search{position:absolute;left:342px;top:159px;width:76px;height:24px;background:linear-gradient(var(--orange-top),var(--orange-dark));border-radius:3px;color:var(--white);font:500 12px/24px "Ubuntu",sans-serif;text-align:center;box-shadow:0 2px 6px rgba(0,40,90,.4)}

.section-title{position:absolute;left:30px;top:366px;color:var(--heading-blue);font:700 16px/1 "Open Sans",sans-serif}
.card{position:absolute;width:201px;height:158px;overflow:hidden;box-shadow:0 1px 2px rgba(0,0,0,.3)}
.card .photo{position:absolute;inset:0}
.card .caption{position:absolute;left:0;bottom:0;width:100%;height:40px;background:var(--caption-bg);color:var(--white);font-family:"Open Sans",sans-serif}
.caption .name{position:absolute;left:13px;top:10px;font-weight:700;font-size:8.5px}
.caption .desc{position:absolute;left:13px;top:24px;font-size:7px}
.caption .tag{position:absolute;right:14px;top:7px;font-size:7px}
.caption .price{position:absolute;right:14px;top:18px;font-size:12px;font-weight:600;color:var(--price-yellow)}

.info-band{position:absolute;left:0;top:946px;width:719px;height:254px;background:var(--gray-band)}
.feature{position:absolute;top:26px;height:60px}
.feature svg{position:absolute;top:0}
.feature h3{position:absolute;top:9px;font:400 13px/1 "Ubuntu",sans-serif;color:var(--gray-text);white-space:nowrap}
.feature p{position:absolute;top:25px;width:104px;font:300 8px/12.8px "Ubuntu",sans-serif;color:var(--gray-light)}
.newsletter-label{position:absolute;left:38px;top:130px;font:400 10.5px/1 "Ubuntu",sans-serif;color:var(--gray-text)}
.newsletter-input{position:absolute;left:37px;top:146px;width:177px;height:22px;background:var(--white)}
.btn-subscribe{position:absolute;left:214px;top:146px;width:65px;height:22px;background:var(--subscribe);border-radius:0 2px 2px 0;color:var(--white);font:400 10px/22px "Ubuntu",sans-serif;text-align:center}
.rule{position:absolute;left:30px;top:184px;width:658px;height:1px;background:#cfcfcf}
.footer-links{position:absolute;left:38px;top:200px;font:500 8.5px/1 "Ubuntu",sans-serif;color:var(--gray-text)}
.copyright{position:absolute;left:38px;top:220px;font:300 7px/1 "Ubuntu",sans-serif;color:var(--gray-light)}
</style>
</head>
<body>
<header class="site-header">
  <div class="brand">STAYSCOUT</div>
  <div class="social" aria-label="Social links"><span></span><span></span><span></span><span></span></div>
</header>

<section class="hero">
  <div class="hero-art" role="img" aria-label="Blue backdrop with faint travel motifs, lit around the search form"></div>
  <h1 class="hero-title">Search Your Best Hotel Now!</h1>
  <p class="hero-sub">Lorem ipsum dolor sit amet, consectetuer adipiscing elit. Nam cursus. Morbi ut mi.</p>
  <div class="field" style="left:38px;top:106px;width:225px;height:28px;padding-left:15px">Hotel, Name, address or landmark</div>
  <div class="field select" style="left:282px;top:106px;width:211px;height:28px;padding-left:15px">City/Locations etc</div>
  <span class="label" style="left:41px;top:145px">When</span>
  <span class="label" style="left:198px;top:145px">Rooms</span>
  <span class="label" style="left:265px;top:145px">Guests</span>
  <div class="field select small" style="left:40px;top:159px;width:63px;height:24px">In time</div>
  <div class="field select small" style="left:107px;top:159px;width:64px;height:24px">out time</div>
  <div class="field select small" style="left:198px;top:159px;width:63px;height:24px">01</div>
  <div class="field select small" style="left:266px;top:159px;width:63px;height:24px">2g</div>
  <div class="btn-search">Search</div>
</section>

<h2 class="section-title">Popular Destinations</h2>

<article class="card" style="left:32px;top:395px"><div class="photo" role="img" aria-label="Hotel tower lit at dusk" style="background:linear-gradient(#6a5a8e,#b88aa0 45%,#3a2c3a)"></div><div class="caption"><span class="name">NAME GOES HERE</span><span class="desc">Lorem ipsum dolor sit</span><span class="tag">Ut ante enim</span><span class="price">$100,000</span></div></article>
<article class="card" style="left:259px;top:395px"><div class="photo" role="img" aria-label="Pool terrace at twilight" style="background:linear-gradient(#3a78c0,#6f8fa8 45%,#5a4a3a)"></div><div class="caption"><span class="name">NAME GOES HERE</span><span class="desc">Lorem ipsum dolor sit</span><span class="tag">Ut ante enim</span><span class="price">$100,000</span></div></article>
<article class="card" style="left:486px;top:395px"><div class="photo" role="img" aria-label="Modern hotel with parasols on a terrace" style="background:linear-gradient(#4c6278,#b9c4cc 55%,#6a7a5a)"></div><div class="caption"><span class="name">NAME GOES HERE</span><span class="desc">Lorem ipsum dolor sit</span><span class="tag">Ut ante enim</span><span class="price">$100,000</span></div></article>

<article class="card" style="left:32px;top:573px"><div class="photo" role="img" aria-label="Thatched restaurant lit at night" style="background:linear-gradient(#8a8fa8,#8a5a3a 45%,#2a2018)"></div><div class="caption"><span class="name">NAME GOES HERE</span><span class="desc">Lorem ipsum dolor sit</span><span class="tag">Ut ante enim</span><span class="price">$100,000</span></div></article>
<article class="card" style="left:259px;top:573px"><div class="photo" role="img" aria-label="Resort pool with palm trees" style="background:linear-gradient(#4f8fce,#a9c6de 55%,#2f8fc0)"></div><div class="caption"><span class="name">NAME GOES HERE</span><span class="desc">Lorem ipsum dolor sit</span><span class="tag">Ut ante enim</span><span class="price">$100,000</span></div></article>
<article class="card" style="left:486px;top:573px"><div class="photo" role="img" aria-label="Grand hotel facade at dusk" style="background:linear-gradient(#5d7fb0,#c79a70 55%,#3a3020)"></div><div class="caption"><span class="name">NAME GOES HERE</span><span class="desc">Lorem ipsum dolor sit</span><span class="tag">Ut ante enim</span><span class="price">$100,000</span></div></article>

<article class="card" style="left:32px;top:750px"><div class="photo" role="img" aria-label="Glass hotel building at night" style="background:linear-gradient(#1a4fb8,#2a60c8 50%,#1a2a50)"></div><div class="caption"><span class="name">NAME GOES HERE</span><span class="desc">Lorem ipsum dolor sit</span><span class="tag">Ut ante enim</span><span class="price">$100,000</span></div></article>
<article class="card" style="left:259px;top:750px"><div class="photo" role="img" aria-label="Beach resort with pool and palms" style="background:linear-gradient(#5a9ad8,#d8d2c0 50%,#2a6a90)"></div><div class="caption"><span class="name">NAME GOES HERE</span><span class="desc">Lorem ipsum dolor sit</span><span class="tag">Ut ante enim</span><span class="price">$100,000</span></div></article>
<article class="card" style="left:486px;top:750px"><div class="photo" role="img" aria-label="Waterfront hotel with turrets" style="background:linear-gradient(#2aa8e0,#9fc8e8 50%,#3a6a8a)"></div><div class="caption"><span class="name">NAME GOES HERE</span><span class="desc">Lorem ipsum dolor sit</span><span class="tag">Ut ante enim</span><span class="price">$100,000</span></div></article>

<section class="info-band">
  <div class="feature" style="left:60px">
    <svg style="left:0" width="32" height="50" viewBox="0 0 32 50" aria-hidden="true"><rect x="2" y="1" width="28" height="4" fill="#848484"/><rect x="2" y="45" width="28" height="4" fill="#848484"/><path d="M6 5 L26 5 L16 25 L26 45 L6 45 L16 25 Z" fill="none" stroke="#848484" stroke-width="2"/><path d="M10 41 L22 41 L16 33 Z" fill="#848484"/></svg>
    <h3 style="left:42px">SAVE TIME</h3>
    <p style="left:43px">Lorem ipsum dolor sit amet, consectetuer adipiscing elit. Nam cursus. Morbi ut mi.</p>
  </div>
  <div class="feature" style="left:270px">
    <svg style="left:0" width="40" height="50" viewBox="0 0 40 50" aria-hidden="true"><circle cx="23" cy="6" r="5" fill="#848484"/><ellipse cx="20" cy="33" rx="17" ry="11" fill="#848484"/><rect x="9" y="40" width="5" height="7" fill="#848484"/><rect x="25" y="40" width="5" height="7" fill="#848484"/></svg>
    <h3 style="left:57px">SAVE TIME</h3>
    <p style="left:58px">Lorem ipsum dolor sit amet, consectetuer adipiscing elit. Nam cursus. Morbi ut mi.</p>
  </div>
  <div class="feature" style="left:486px">
    <svg style="left:0" width="54" height="50" viewBox="0 0 54 50" aria-hidden="true"><rect x="0" y="20" width="54" height="2" fill="#848484"/><rect x="8" y="26" width="38" height="20" rx="2" fill="#848484"/><g fill="#848484"><circle cx="9" cy="14" r="3"/><circle cx="18" cy="14" r="3"/><circle cx="27" cy="14" r="3"/><circle cx="36" cy="14" r="3"/><circle cx="45" cy="14" r="3"/></g></svg>
    <h3 style="left:67px">SAVE TIME</h3>
    <p style="left:68px">Lorem ipsum dolor sit amet, consectetuer adipiscing elit. Nam cursus. Morbi ut mi.</p>
  </div>

  <div class="newsletter-label">SIGN UP NEWSLETTERS HERE</div>
  <div class="newsletter-input"></div>
  <div class="btn-subscribe">Subscribe</div>
  <div class="rule"></div>
  <div class="footer-links">ABOUT US &nbsp;|&nbsp; CONTACT US</div>
  <div class="copyright">© 2013 Company Name. &nbsp;All right reserved. &nbsp;Term of Use</div>
</section>
</body>
</html>
```